Design a business card
Business name: Harbourline Growth Advisory
Improving Business Profitibility

- An Overview of the Business & Service:

Business Performance Consulting

- The Target Market: Small to medium-sized business

- Design Specifics:
White card, blue ink, moon eclipse

No Logo

Target Market(s)

Small to medium-sized business

Font styles to use
Sans Serif

```html
<!DOCTYPE html>
<html lang="en">
<head>
<meta charset="utf-8">
<title>Harbourline Growth Advisory – Business Card</title>
<link rel="stylesheet" href="https://fonts.googleapis.com/css2?family=Bebas+Neue&family=Open+Sans:wght@400;600&display=swap">
<style>
  :root {
    --backdrop: #2b2b2b;
    --card-white: #eeeeee;
    --brand-blue: #3672b3;
    --ink-dark: #2f2f2f;
    --rule-grey: #a9a9a9;
    --tagline: #c9d7ea;
    --white: #ffffff;
  }
  html, body {
    margin: 0;
    padding: 0;
    width: 1200px;
    height: 1200px;
    overflow: hidden;
    background: var(--backdrop);
  }
  .canvas {
    position: relative;
    width: 1200px;
    height: 1200px;
  }
  .card {
    position: absolute;
    top: 310px;
    height: 594px;
    box-sizing: border-box;
    text-align: center;
  }
  .card--front {
    left: 234px;
    width: 364px;
    background: var(--card-white);
    color: var(--ink-dark);
  }
  .card--back {
    left: 627px;
    width: 369px;
    background: var(--brand-blue);
    color: var(--white);
  }
  .wordmark {
    position: absolute;
    left: 0;
    right: 0;
    font-family: "Bebas Neue", "Arial Narrow", sans-serif;
    line-height: 1;
  }
  .card--front .wordmark { top: 158px; color: var(--brand-blue); }
  .card--back .wordmark { top: 262px; color: var(--white); }
  .wordmark__top {
    font-size: 41px;
    letter-spacing: 0.2px;
  }
  .wordmark__bottom {
    display: flex;
    align-items: center;
    justify-content: center;
    gap: 8px;
    margin-top: 0;
    font-size: 36px;
  }
  .wordmark__rule {
    display: block;
    width: 67px;
    height: 3px;
    background: currentColor;
  }
  .contact {
    position: absolute;
    top: 330px;
    left: 0;
    right: 0;
    font-family: "Open Sans", Arial, sans-serif;
    font-size: 17px;
    line-height: 21.5px;
  }
  .contact__name {
    font-family: "Bebas Neue", "Arial Narrow", sans-serif;
    font-size: 31px;
    line-height: 1;
    color: var(--brand-blue);
  }
  .contact__role { margin-top: 0; }
  .contact__divider {
    width: 208px;
    height: 1px;
    margin: 8px auto 10px;
    background: var(--rule-grey);
  }
  .contact__label {
    color: var(--brand-blue);
    font-weight: 600;
  }
  .contact__web {
    color: var(--brand-blue);
    font-weight: 600;
  }
  .tagline {
    position: absolute;
    top: 524px;
    left: 0;
    right: 0;
    font-family: "Open Sans", Arial, sans-serif;
    font-size: 16px;
    color: var(--tagline);
    letter-spacing: 0.1px;
  }
</style>
</head>
<body>
<main class="canvas">
  <section class="card card--front" aria-label="Business card front">
    <div class="wordmark">
      <div class="wordmark__top">HARBOURLINE GROWTH</div>
      <div class="wordmark__bottom"><span class="wordmark__rule"></span>ADVISORY<span class="wordmark__rule"></span></div>
    </div>
    <div class="contact">
      <div class="contact__name">DESMOND R AKERLY</div>
      <div class="contact__role">Managing Director</div>
      <div class="contact__divider"></div>
      <div><span class="contact__label">P:</span> 031-468 220 517</div>
      <div><span class="contact__label">M:</span> 031-468 220 518</div>
      <div><span class="contact__label">E:</span> hello@harbourline.co</div>
      <div class="contact__web">www.harbourline.co</div>
      <div class="contact__divider"></div>
      <div>48, Wharf Lane Suite 3</div>
      <div>Port Avelin, 504219.</div>
    </div>
  </section>

  <section class="card card--back" aria-label="Business card back">
    <div class="wordmark">
      <div class="wordmark__top">HARBOURLINE GROWTH</div>
      <div class="wordmark__bottom"><span class="wordmark__rule"></span>ADVISORY<span class="wordmark__rule"></span></div>
    </div>
    <div class="tagline">IMPROVING BUSINESS PROFITIBILITY</div>
  </section>
</main>
</body>
</html>
```